Hollow Thicket, a 3d voxel survival video game needs a card for gaming conventions

I am the lead developer for Hollow Thicket http://www.HollowThicket.example and need a business card to hand out at an indie gaming convention
The card would need to include the game name, website url, my name, position (Lead Developer), e-mail and phone number
The game is a 3d, voxel (with smooth terrain) based survival game with guns and wildlife. The main icon of the game would likely be a grizzly bear but I am willing to accept other designs too.
Attached is a media kit for the game with some images you can use but don't have to its just what little art I can provide. Anything on the website or from the video game can also be used. unrelated art can also be used.
Target Market(s)
Indie Developers/publishers at conferences
Industry/Entity Type
Games
Contact Information for Business Card
Name: Corin Waldrick
Position: Lead Developer
E-mail: Pale_Kettle@mailbox.example
Phone number: 555-372-1186

```html
<!DOCTYPE html>
<html lang="en">
<head>
<meta charset="utf-8">
<title>Hollow Thicket – Business Card</title>
<link href="https://fonts.googleapis.com/css2?family=Source+Sans+3:wght@400;600;700&display=swap" rel="stylesheet">
<style>
  :root {
    --backdrop: #000000;
    --card: #323337;
    --card-edge: #393a3f;
    --accent: #c9542b;
    --text-light: #ececec;
    --logo-tan: #b9a06a;
    --fur-dark: #3b2114;
    --fur-mid: #6e3e22;
    --fur-light: #9a5f36;
  }
  * { margin: 0; padding: 0; box-sizing: border-box; }
  html, body {
    width: 1200px; height: 900px; overflow: hidden;
    background: var(--backdrop);
    font-family: "Source Sans 3", "Myriad Pro", sans-serif;
  }
  .canvas { position: relative; width: 1200px; height: 900px; }
  .card {
    position: absolute; top: 271px; width: 457px; height: 282px;
    background: var(--card);
    border-radius: 14px;
    overflow: hidden;
    box-shadow: inset 0 0 0 1px var(--card-edge);
  }
  .card--front { left: 137px; }
  .card--back { left: 626px; }

  .mascot-photo {
    position: absolute; left: -30px; top: 30px; width: 190px; height: 232px;
    background:
      radial-gradient(ellipse 45% 40% at 62% 30%, var(--fur-light) 0%, var(--fur-mid) 55%, transparent 100%),
      radial-gradient(ellipse 60% 60% at 45% 55%, var(--fur-mid) 0%, var(--fur-dark) 70%, transparent 100%);
    -webkit-mask-image: radial-gradient(ellipse 52% 50% at 50% 45%, #000 55%, transparent 100%);
            mask-image: radial-gradient(ellipse 52% 50% at 50% 45%, #000 55%, transparent 100%);
  }

  .contact { position: absolute; left: 204px; top: 98px; }
  .contact__name {
    font-size: 17px; font-weight: 600; color: var(--accent); line-height: 20px;
  }
  .contact__role {
    font-size: 15.5px; font-weight: 400; color: var(--text-light); line-height: 19px;
  }
  .contact__list { list-style: none; margin-top: 30px; }
  .contact__item {
    display: flex; align-items: center; gap: 8px;
    font-size: 15px; color: var(--text-light); line-height: 19px;
  }
  .contact__icon { width: 12px; height: 12px; flex: none; }

  .game-name {
    position: absolute; inset: 0;
    display: flex; align-items: center; justify-content: center;
    font-size: 36px; font-weight: 700; letter-spacing: 3px;
    color: var(--logo-tan); text-transform: uppercase;
    padding-bottom: 3px;
  }
</style>
</head>
<body>
<div class="canvas">
  <section class="card card--front">
    <div class="mascot-photo" role="img" aria-label="Photo of a roaring grizzly bear"></div>
    <div class="contact">
      <p class="contact__name">Corin Waldrick</p>
      <p class="contact__role">Lead Developer</p>
      <ul class="contact__list">
        <li class="contact__item">
          <svg class="contact__icon" viewBox="0 0 12 12" aria-hidden="true">
            <path d="M2.5 1 L4.5 1 L5.3 3.6 L4 4.6 C4.7 6.1 5.9 7.3 7.4 8 L8.4 6.7 L11 7.5 L11 9.5 C11 10.3 10.3 11 9.5 11 C5 11 1 7 1 2.5 C1 1.7 1.7 1 2.5 1 Z" fill="var(--accent)"/>
          </svg>
          555-372-1186
        </li>
        <li class="contact__item">
          <svg class="contact__icon" viewBox="0 0 12 12" aria-hidden="true">
            <rect x="1" y="3" width="10" height="7" fill="var(--accent)"/>
            <path d="M1 3 L6 7 L11 3" fill="none" stroke="var(--card)" stroke-width="1"/>
          </svg>
          Pale_Kettle@mailbox.example
        </li>
        <li class="contact__item">
          <svg class="contact__icon" viewBox="0 0 12 12" aria-hidden="true">
            <circle cx="6" cy="6" r="4.5" fill="none" stroke="var(--accent)" stroke-width="1.2"/>
            <path d="M1.5 6 H10.5 M6 1.5 C4 4 4 8 6 10.5 M6 1.5 C8 4 8 8 6 10.5" fill="none" stroke="var(--accent)" stroke-width="1"/>
          </svg>
          www.HollowThicket.example
        </li>
      </ul>
    </div>
  </section>

  <section class="card card--back">
    <h1 class="game-name">Hollow Thicket</h1>
  </section>
</div>
</body>
</html>
```